A5, portrait
Theme is science
audience is VIPS, politicians, executives
this is a really important event, we want a very classy invitation
include logo for bloom and grow and lantern but lantern one bigger
images attached
Have attached some styles we like but doesn't need to be these colours. If we can incorporate some colours from our logo would be good but don't make too colourful and childish

You’re invited to the official opening and launch of Lantern, Centre of Discovery. an industry first, pioneering, STEM hub.

Saturday 30th April, 2022

10:00 am – 12:00 pm

42 Harlow Lane, Fernwood

Light canapes provided. Dress code is smart/casual

All guests will be given a guided walk through of Australia’s first dedicated STEM education hub for children aged 3-6.

Invitation only

RSVP: 18 April to marketing@bloomandgrow.edu.au

```html
<!DOCTYPE html>
<html lang="en">
<head>
<meta charset="utf-8">
<title>Lantern, Centre of Discovery – Opening Invitation</title>
<link href="https://fonts.googleapis.com/css2?family=Playfair+Display:wght@400;700&display=swap" rel="stylesheet">
<style>
  :root {
    --page-bg: #e4e5e8;
    --navy-top: #2b3968;
    --navy-mid: #45588a;
    --navy-bottom: #6883ae;
    --gold: #d8b424;
    --ink: #ffffff;
    --sky: #0fb0ec;
    --photo-a: #2a2f6e;
    --photo-b: #8a76c4;
  }
  * { margin: 0; padding: 0; box-sizing: border-box; }
  html, body { width: 960px; height: 1200px; overflow: hidden; }
  body {
    background: var(--page-bg);
    font-family: "Playfair Display", Georgia, serif;
    color: var(--ink);
    position: relative;
  }
  .invitation {
    position: absolute;
    left: 46px; top: 0;
    width: 867px; height: 1200px;
    overflow: hidden;
    background: linear-gradient(180deg, var(--navy-top) 0%, var(--navy-mid) 50%, var(--navy-bottom) 100%);
  }
  .frame { position: absolute; inset: 0; }
  .center-text { position: absolute; left: 0; width: 100%; text-align: center; }
  .headline {
    top: 92px; font-size: 50px; font-weight: 700; letter-spacing: 0.5px; line-height: 1;
  }
  .headline span { display: inline-block; border-bottom: 1.5px solid var(--ink); padding-bottom: 8px; }
  .lede { top: 162px; font-size: 19px; }
  .venue-mark { top: 350px; line-height: 1; font-weight: 700; }
  .venue-mark .name { font-size: 62px; letter-spacing: 3px; display: block; }
  .venue-mark .tagline { font-size: 24px; margin-top: 16px; display: block; }
  .strapline { top: 575px; font-size: 19px; }
  .detail {
    position: absolute; text-align: center; font-size: 18.5px; line-height: 28px;
  }
  .detail-date { left: 127px; width: 200px; top: 646px; }
  .detail-time { left: 363px; width: 140px; top: 636px; line-height: 20px; }
  .detail-time span { display: block; }
  .detail-time .dash { line-height: 12px; margin: 1px 0 3px; }
  .detail-place { left: 537px; width: 200px; top: 646px; }
  .note { position: absolute; top: 746px; font-size: 18.5px; text-align: center; }
  .note-food { left: 173px; width: 240px; }
  .note-dress { left: 456px; width: 268px; }
  .tour {
    position: absolute; left: 107px; top: 808px; width: 365px;
    font-size: 17.5px; line-height: 25px;
  }
  .access-badge {
    position: absolute; left: 106px; top: 893px; width: 178px; height: 36px;
    border: 1px solid var(--gold); border-radius: 18px;
    color: var(--gold); font-size: 16px; text-align: center; line-height: 34px;
  }
  .rsvp { position: absolute; left: 107px; top: 944px; font-size: 17.5px; white-space: nowrap; }
  .rsvp strong { color: var(--gold); font-weight: 700; }
  .hub-photo {
    position: absolute; left: 543px; top: 824px; width: 214px; height: 214px; border-radius: 50%;
    background: radial-gradient(circle at 50% 45%, #c9c4f0 0%, var(--photo-b) 30%, var(--photo-a) 75%, #14163a 100%);
  }
  .host-mark {
    position: absolute; left: 369px; top: 1038px; width: 130px; height: 162px;
    background: var(--sky); border-radius: 8px 8px 0 0;
    display: flex; align-items: center; justify-content: center; text-align: center;
    font-size: 22px; font-weight: 700; line-height: 1.1; color: var(--ink);
  }
</style>
</head>
<body>
<main class="invitation">
  <svg class="frame" width="867" height="1200" viewBox="0 0 867 1200" fill="none">
    <g stroke="#d8b424" stroke-width="1.4">
      <path d="M445 45 H787 A34 34 0 0 1 821 79 V1120 A34 34 0 0 1 787 1154 H603"/>
      <path d="M265 1154 H79 A34 34 0 0 1 45 1120 V79 A34 34 0 0 1 79 45 H422"/>
    </g>
    <circle cx="433.5" cy="45" r="4" fill="#d8b424"/>
    <g stroke="#d8b424" stroke-width="0.9" opacity="0.85">
      <path d="M137 622 H424 M443 622 H731"/>
      <path d="M137 731 H731"/>
      <path d="M137 789 H424 M443 789 H731"/>
      <path d="M346 642 V718 M520 642 V718 M433.5 740 V770"/>
    </g>
    <circle cx="433.5" cy="622" r="3.5" fill="#d8b424"/>
    <circle cx="433.5" cy="789" r="3.5" fill="#d8b424"/>
    <circle cx="650" cy="931" r="118" stroke="#d8b424" stroke-width="1.3"/>
  </svg>

  <h1 class="center-text headline"><span>YOU’RE INVITED</span></h1>
  <p class="center-text lede">to the official opening and launch of</p>

  <div class="center-text venue-mark">
    <span class="name">LANTERN</span>
    <span class="tagline">Centre of Discovery</span>
  </div>

  <p class="center-text strapline">An industry first, pioneering, STEM hub</p>

  <p class="detail detail-date">Saturday,<br>30th April, 2022</p>
  <p class="detail detail-time"><span>10:00 am</span><span class="dash">–</span><span>12:00 pm</span></p>
  <p class="detail detail-place">42 Harlow Lane,<br>Fernwood</p>

  <p class="note note-food">Light canapes provided</p>
  <p class="note note-dress">Dress code is smart/casual</p>

  <p class="tour">All guests will be given a guided walk through of Australia’s first dedicated STEM education hub for children aged 3-6.</p>
  <p class="access-badge">INVITATION ONLY</p>
  <p class="rsvp"><strong>RSVP:</strong> 18 April to marketing@bloomandgrow.edu.au</p>

  <div class="hub-photo" role="img" aria-label="Photo of a glowing plasma globe on display inside the STEM hub"></div>

  <div class="host-mark">Bloom<br>&amp; Grow</div>
</main>
</body>
</html>
```